HARBORLINE AUTO GLASS

Mobile Glass Shop:

1) Windshield REPAIR 2)Windshield replacment 3) Rear Windshield Replacment 4) Side Window Replacment 5) car window replacment 6) Power Window Repair.

Schedual a service within 24 hour with one of our certified technicians.
Updates

See "brightvane auto repair" web site for referance on the nature of our buisness and service. www.brightvane-example.com

Coding

```html
<!DOCTYPE html>
<html lang="en">
<head>
<meta charset="utf-8">
<title>Harborline Auto Glass</title>
<link href="https://fonts.googleapis.com/css2?family=Montserrat:wght@400;500;600;700;800&display=swap" rel="stylesheet">
<style>
:root{
  --navy:#05054a;
  --navy-deep:#020236;
  --card:#040440;
  --brand:#0a6bb5;
  --sky:#1fa9e0;
  --mist:#e4ecef;
  --link:#0a5aa8;
  --white:#ffffff;
  --ink:#111111;
  --button:#0b5fa5;
}
*{margin:0;padding:0;box-sizing:border-box}
html,body{width:667px;height:1200px;overflow:hidden}
body{position:relative;font-family:"Montserrat",sans-serif;background:var(--white)}
.abs{position:absolute}

/* nav */
.site-nav{position:absolute;left:0;top:0;width:667px;height:31px;background:var(--white);border-top:1px solid var(--navy)}
.brand{position:absolute;display:flex;align-items:center;gap:3px;color:var(--brand);font-weight:800;font-size:6.4px;letter-spacing:.1px;white-space:nowrap}
.brand-mark{width:9px;height:9px;background:var(--brand);border-radius:1px}
.nav-link{position:absolute;top:11px;font-size:9px;color:var(--brand);font-weight:500}
.nav-link.active{color:var(--sky);border-bottom:1px solid var(--sky);padding:0 3px 2px}
.quote-btn{position:absolute;left:546px;top:6.5px;width:73px;height:20px;background:var(--button);color:var(--white);font-size:7.5px;font-weight:700;border-radius:2px;display:flex;align-items:center;justify-content:center}

/* hero */
.hero{position:absolute;left:0;top:31px;width:667px;height:437px;background:var(--navy)}
.hero-top{position:absolute;left:0;top:0;width:667px;height:302px;background:radial-gradient(ellipse at 60% 40%,#14147a 0%,#07075a 45%,var(--navy-deep) 100%)}
.photo-van{position:absolute;left:0;top:53px;width:202px;height:200px;background:linear-gradient(90deg,#c9c9cf,#eeeef2 60%,#b6b6bc);border-radius:0 30px 14px 0}
.photo-car{position:absolute;left:419px;top:39px;width:195px;height:256px;background:radial-gradient(ellipse at 45% 45%,#3a3a8a 0%,#1b1b66 50%,rgba(7,7,90,0) 75%)}
.hero-eyebrow{position:absolute;left:0;width:640px;top:123px;text-align:center;color:var(--white);font-size:5.6px;font-weight:500}
.hero-title{position:absolute;left:0;width:640px;top:136px;text-align:center;color:var(--brand);font-size:17.5px;font-weight:800;line-height:16px}
.hero-sub{position:absolute;left:0;width:640px;top:175px;text-align:center;color:var(--sky);font-size:8px;line-height:11px}
.more-btn{position:absolute;left:282px;top:215px;width:52px;height:14px;border-radius:7px;background:var(--button);color:var(--white);font-size:6.8px;font-weight:700;display:flex;align-items:center;justify-content:center}
.feature{position:absolute;top:317px;width:119px;height:126px;background:var(--card);border-radius:6px;box-shadow:0 3px 8px rgba(0,0,0,.35);text-align:center}
.feature svg{position:absolute;left:50%;transform:translateX(-50%);top:10px}
.feature h3{position:absolute;left:0;width:100%;top:50px;color:var(--brand);font-size:9.6px;font-weight:500}
.feature hr{position:absolute;left:12px;width:95px;top:68px;border:0;border-top:.6px solid #3c3c8a}
.feature p{position:absolute;left:10px;width:99px;top:77px;color:var(--sky);font-size:5.8px;line-height:7.4px;font-weight:500}

/* why us */
.why{position:absolute;left:0;top:468px;width:667px;height:182px;background:var(--mist)}
.photo-fitting{position:absolute;left:57px;top:13px;width:265px;height:156px;border-radius:23px 0 23px 0;background:linear-gradient(120deg,#6f72c9,#b9bdf0 40%,#3b3f9e 75%,#23277a)}
.eyebrow{position:absolute;left:360px;top:27px;font-size:5.6px;color:#333}
.why h2{position:absolute;left:360px;top:34px;font-size:18px;font-weight:800;color:var(--brand)}
.why .rule{position:absolute;left:360px;top:58px;width:190px;border-top:.8px solid var(--brand)}
.why p{position:absolute;left:362px;width:195px;font-size:7.5px;line-height:8.4px;color:var(--ink)}

/* services */
.services{position:absolute;left:0;top:650px;width:667px;height:235px;background:var(--navy)}
.tile{position:absolute;display:flex;align-items:center;justify-content:center;text-align:center;color:var(--white);font-size:9.5px;font-weight:800;line-height:11px;background:linear-gradient(135deg,#0a3f96,#0b52a8 50%,#083b86)}
.tile.dark{background:linear-gradient(135deg,#04123a,#0a2a6e 60%,#061a4d)}
.services h2{position:absolute;left:0;width:672px;top:35px;text-align:center;color:var(--brand);font-size:18px;font-weight:800}
.services .rule{position:absolute;left:270px;width:132px;top:70px;border-top:.8px solid var(--brand)}
.services p{position:absolute;left:268px;width:136px;text-align:center;color:var(--white);font-size:7.5px;line-height:8.4px}
.read-btn{position:absolute;left:302px;top:184px;width:64px;height:15px;border:1px solid var(--white);color:var(--white);font-size:7.5px;font-weight:700;display:flex;align-items:center;justify-content:center}

/* contact */
.contact{position:absolute;left:0;top:885px;width:667px;height:174px;background:radial-gradient(ellipse at 55% 60%,#0b5ea8 0%,#0a4a93 45%,#082f78 100%)}
.photo-agent{position:absolute;left:127px;top:15px;width:137px;height:137px;border-radius:50%;background:radial-gradient(circle at 50% 45%,#f4ede8,#e4ddd8 60%,#c9c3bf)}
.contact h2{position:absolute;left:347px;top:24px;color:var(--white);font-size:18px;font-weight:800;word-spacing:3px}
.field{position:absolute;left:349px;width:210px;border:.8px solid var(--white);color:var(--white);font-size:6.2px;padding:2px 3px}
.send-btn{position:absolute;left:349px;top:141px;width:42px;height:15px;border:.8px solid var(--white);color:var(--white);font-size:7.5px;font-weight:700;display:flex;align-items:center;justify-content:center}

/* footer */
.footer{position:absolute;left:0;top:1059px;width:667px;height:120px;background:var(--mist)}
.footer-about{position:absolute;left:57px;top:50px;width:180px;color:var(--link);font-size:5.9px;line-height:7.4px}
.footer .divider{position:absolute;left:57px;top:88px;width:178px;border-top:.8px solid var(--link)}
.social{position:absolute;top:96px;width:10px;height:10px;background:var(--button);border-radius:2px}
.footer h4{position:absolute;top:11px;color:var(--link);font-size:8.8px;font-weight:800}
.footer h4::after{content:"";position:absolute;left:0;top:14px;width:72px;border-top:.8px solid var(--link)}
.footer ul{position:absolute;list-style:none;top:32px}
.footer li{color:var(--link);font-size:7px;height:14px;line-height:8px}
.copyright{position:absolute;left:0;top:1179px;width:667px;height:21px;background:var(--navy);color:var(--sky);font-size:6px;display:flex;align-items:center;justify-content:center}
</style>
</head>
<body>

<header class="site-nav">
  <div class="brand" style="left:63px;top:11px"><span class="brand-mark"></span>HARBORLINE AUTO GLASS</div>
  <nav>
    <span class="nav-link active" style="left:252px">Home</span>
    <span class="nav-link" style="left:307px">About us</span>
    <span class="nav-link" style="left:373px">Services</span>
    <span class="nav-link" style="left:437px">Locations</span>
  </nav>
  <div class="quote-btn">Get Quote</div>
</header>

<section class="hero">
  <div class="hero-top"></div>
  <div class="photo-van" role="img" aria-label="White service van with company lettering"></div>
  <div class="photo-car" role="img" aria-label="Dark sports car with lit headlights"></div>
  <div class="hero-eyebrow">MOBILE GLASS SHOP</div>
  <h1 class="hero-title">Windshield Repair,<br>Replacement</h1>
  <div class="hero-sub">Schedual a service within 24 hour with one<br>of our certified technicians.</div>
  <div class="more-btn">More Info</div>

  <div class="feature" style="left:109px">
    <svg width="40" height="32" viewBox="0 0 40 32">
      <path d="M1 12 L11 9 L11 31 L1 31 Z M13 9 L26 13 L26 31 L13 28 Z M28 13 L39 9 L39 28 L28 31 Z" fill="#0a6bb5"/>
      <path d="M20 0 a8 8 0 0 1 8 8 c0 6 -8 14 -8 14 s-8 -8 -8 -14 a8 8 0 0 1 8 -8 z" fill="#0a6bb5" stroke="#040440" stroke-width="1.5"/>
      <circle cx="20" cy="8" r="3" fill="#040440"/>
    </svg>
    <h3>AT YOUR HOME</h3><hr>
    <p>Lorem ipsum dolor sit amet, consectetur adipiscing elit. Orci, eu lorem vitae natoque dictum posuere. Sed vitae vestibulum vel vitae.</p>
  </div>
  <div class="feature" style="left:262px">
    <svg width="32" height="32" viewBox="0 0 32 32">
      <circle cx="16" cy="15" r="14" fill="#0a6bb5"/>
      <path d="M9 15 L14 20 L23 11" fill="none" stroke="#040440" stroke-width="3.2" stroke-linecap="round" stroke-linejoin="round"/>
    </svg>
    <h3 style="top:49px;font-size:9px">WARRANTY PROCESS</h3><hr>
    <p>Lorem ipsum dolor sit amet, consectetur adipiscing elit. Orci, eu lorem vitae natoque dictum posuere. Sed vitae vestibulum vel vitae.</p>
  </div>
  <div class="feature" style="left:413px">
    <svg width="34" height="32" viewBox="0 0 34 32">
      <g fill="none" stroke="#0a6bb5" stroke-width="3.5" stroke-linejoin="round">
        <path d="M12 5 L17 2 L22 10"/>
        <path d="M28 17 L31 23 L24 28 L17 28"/>
        <path d="M8 28 L3 24 L8 15"/>
      </g>
      <g fill="#0a6bb5">
        <path d="M18 8 L26 8 L23 15 Z"/>
        <path d="M20 23 L20 32 L14 28 Z"/>
        <path d="M4 14 L12 13 L9 20 Z"/>
      </g>
    </svg>
    <h3>GLASS RECYCLING</h3><hr>
    <p>Lorem ipsum dolor sit amet, consectetur adipiscing elit. Orci, eu lorem vitae natoque dictum posuere. Sed vitae vestibulum vel vitae.</p>
  </div>
</section>

<section class="why">
  <div class="photo-fitting" role="img" aria-label="Technicians fitting a new windshield onto a car"></div>
  <div class="eyebrow">HARBORLINE AUTO GLASS</div>
  <h2>Why Us</h2>
  <div class="rule"></div>
  <p style="top:68px">Lorem ipsum dolor sit amet, consectetur adipiscing elit. Cursus consequat varius ipsum feugiat est tristique morbi. Lectus et cursus condimentum rutrum. At pellentesque mi tortor, id vel urna.</p>
  <p style="top:112px">Lorem ipsum dolor sit amet, consectetur adipiscing elit. Cursus consequat varius ipsum feugiat est tristique morbi. Lectus et cursus condimentum rutrum. At pellentesque mi tortor, id vel urna. Turpis suspendisse libero proin eu nulla venenatis auctor. Urna odio a ipsum leo tortor sagittis.</p>
</section>

<section class="services">
  <div class="tile" style="left:57px;top:41px;width:82px;height:74px" role="img" aria-label="Windshield repair work">WINDSHIELD<br>REPAIR</div>
  <div class="tile" style="left:152px;top:41px;width:82px;height:74px" role="img" aria-label="Windshield replacement work">WINDSHIELD<br>REPLACEMENT</div>
  <div class="tile" style="left:57px;top:124px;width:177px;height:74px" role="img" aria-label="Rear windshield with wiper">REAR WINDSHIELD<br>REPLACMENT</div>
  <h2>Our Services</h2>
  <div class="rule"></div>
  <p style="top:86px">Lorem ipsum dolor sit amet, consectetur adipiscing elit. Cursus consequat varius ipsum feugiat est tristique morbi. Lectus et cursus condimentum rutrum. At pellentesque mi tortor, id vel urna.</p>
  <p style="top:150px">Lorem ipsum dolor sit amet, consectetur adipiscing elit.</p>
  <div class="read-btn">Read More</div>
  <div class="tile" style="left:433px;top:41px;width:177px;height:74px" role="img" aria-label="Cleaning a side window">SIDE WINDOW<br>REPLACMENT</div>
  <div class="tile" style="left:433px;top:125px;width:84px;height:73px" role="img" aria-label="Car window being replaced">CAR WINDOW<br>REPLACMENT</div>
  <div class="tile dark" style="left:526px;top:125px;width:84px;height:73px" role="img" aria-label="Technician repairing a power window">POWER<br>WINDOW<br>REPAIR</div>
</section>

<section class="contact">
  <svg class="abs" style="left:110px;top:0" width="170" height="174" viewBox="0 0 170 174">
    <path d="M83 12 A81 81 0 0 1 165 95" fill="none" stroke="#ffffff" stroke-width=".8" opacity=".8"/>
    <path d="M2 85 A81 81 0 0 0 83 167" fill="none" stroke="#ffffff" stroke-width=".8" opacity=".8"/>
  </svg>
  <div class="photo-agent" role="img" aria-label="Support agent with headset"></div>
  <h2>Contact Us</h2>
  <div class="field" style="top:47px;height:13px">NAME</div>
  <div class="field" style="top:66px;height:13px">EMAIL</div>
  <div class="field" style="top:86px;height:50px">Message</div>
  <div class="send-btn">Send</div>
</section>

<footer class="footer">
  <div class="brand" style="left:92px;top:23px"><span class="brand-mark"></span>HARBORLINE AUTO GLASS</div>
  <p class="footer-about">Lorem ipsum dolor sit amet, consectetur adipiscing elit. Mauris non sed eget ut est elit. Ultricies suspendisse habitasse lobortis pellentesque aliquet ac mauris, viverra. Odio fames lacus cursus ut sem.</p>
  <div class="divider"></div>
  <span class="social" style="left:57px"></span>
  <span class="social" style="left:73px"></span>
  <span class="social" style="left:88px"></span>
  <span class="social" style="left:104px"></span>
  <h4 style="left:285px">Quick Links</h4>
  <ul style="left:296px">
    <li>HOME</li><li>SERVICES</li><li>LOCATIONS</li><li>CONTACT US</li>
  </ul>
  <h4 style="left:411px">SERVICES</h4>
  <ul style="left:422px">
    <li>WINDSHIELD REPAIR</li><li>WINDSHIELD REPLACEMENT</li><li>REAR WINDSHIELD REPLACEMENT</li><li>SIDE WINDOW REPLACEMENT</li><li>CAR WINDOW REPLACEMENT</li><li>POWER WINDOW REPAIR</li>
  </ul>
</footer>
<div class="copyright">Copyright © 2022 Northgate Studio. All rights reserved.</div>

</body>
</html>
```